business card deign

Logo needs the following on it.
1. attached logo
2. Tagline - "If it keeps the cooler full or the night rolling...we bring it!"
3. Name- Dalton Pikes, Founder and CPO
4. Address - 412 E. Carver Avenue, Ste 2207, Tampa, FL. 33917
5. Phone - 555.318.4726

```html
<!DOCTYPE html>
<html lang="en">
<head>
<meta charset="utf-8">
<title>Brindle Business Card</title>
<link href="https://fonts.googleapis.com/css2?family=Roboto:wght@400;500;700&display=swap" rel="stylesheet">
<style>
  :root {
    --backdrop: #d9d9d9;
    --card: #161616;
    --ink: #ffffff;
    --rule: #cfcfcf;
    --muted: #e6e6e6;
  }
  * { margin: 0; padding: 0; box-sizing: border-box; }
  html, body { width: 1200px; height: 711px; overflow: hidden; }
  body {
    background: var(--backdrop);
    font-family: "Roboto", Arial, sans-serif;
    color: var(--ink);
    position: relative;
  }
  .card {
    position: absolute;
    width: 540px;
    height: 310px;
    background: var(--card);
    border-radius: 26px;
    box-shadow: 0 10px 24px rgba(0,0,0,0.28);
    overflow: hidden;
  }
  .card--front { left: 70px; top: 50px; }
  .card--back { left: 590px; top: 350px; }

  .brand {
    display: flex;
    align-items: center;
    gap: 14px;
    font-weight: 700;
    letter-spacing: 0.32em;
    color: var(--ink);
  }
  .brand__dot {
    width: 14px; height: 14px;
    border-radius: 50%;
    background: var(--ink);
  }
  .card--front .brand {
    position: absolute;
    left: 50%; top: 50%;
    transform: translate(-50%, -50%);
    font-size: 40px;
  }
  .card--back .brand {
    position: absolute;
    right: 60px; top: 58px;
    font-size: 28px;
  }
  .card--back .brand__dot { width: 10px; height: 10px; }

  .divider {
    position: absolute;
    right: 40px; top: 112px;
    width: 250px; height: 1px;
    background: var(--rule);
  }

  .person {
    position: absolute;
    left: 0; top: 150px;
    padding-left: 42px;
  }
  .person__bar {
    position: absolute;
    left: 0; top: 2px;
    width: 30px; height: 62px;
    background: var(--ink);
  }
  .person__name { font-size: 26px; font-weight: 700; line-height: 1.1; }
  .person__title { font-size: 15px; font-weight: 400; margin-top: 4px; padding-bottom: 8px; border-bottom: 1px solid var(--rule); width: 200px; }

  .tagline {
    position: absolute;
    left: 42px; bottom: 34px;
    font-size: 13px;
    line-height: 1.45;
    color: var(--muted);
  }

  .contact {
    position: absolute;
    right: 40px; top: 150px;
    text-align: right;
    font-size: 13px;
    line-height: 1.6;
    color: var(--muted);
  }
  .contact__row { display: flex; justify-content: flex-end; align-items: center; gap: 8px; }
  .contact__icon { width: 13px; height: 13px; flex: none; }
  .contact__spacer { width: 13px; flex: none; }
</style>
</head>
<body>
  <section class="card card--front">
    <div class="brand"><span class="brand__dot"></span>BRINDLE</div>
  </section>

  <section class="card card--back">
    <div class="brand"><span class="brand__dot"></span>BRINDLE</div>
    <div class="divider"></div>

    <div class="person">
      <span class="person__bar"></span>
      <p class="person__name">Dalton Pikes</p>
      <p class="person__title">Founder and CPO</p>
    </div>

    <div class="contact">
      <div class="contact__row">555.318.4726
        <svg class="contact__icon" viewBox="0 0 24 24"><path fill="#fff" d="M6.6 10.8a15 15 0 0 0 6.6 6.6l2.2-2.2a1 1 0 0 1 1-.25 11.4 11.4 0 0 0 3.6.57 1 1 0 0 1 1 1V20a1 1 0 0 1-1 1A17 17 0 0 1 3 4a1 1 0 0 1 1-1h3.5a1 1 0 0 1 1 1c0 1.25.2 2.45.57 3.57a1 1 0 0 1-.25 1z"/></svg>
      </div>
      <div class="contact__row">412 E. Carver Avenue,
        <svg class="contact__icon" viewBox="0 0 24 24"><path fill="#fff" d="M12 2a7 7 0 0 0-7 7c0 5.2 7 13 7 13s7-7.8 7-13a7 7 0 0 0-7-7zm0 9.5A2.5 2.5 0 1 1 12 6.5a2.5 2.5 0 0 1 0 5z"/></svg>
      </div>
      <div class="contact__row">Ste 2207, Tampa, FL. 33917<span class="contact__spacer"></span></div>
    </div>

    <p class="tagline">If it keeps the cooler full or<br>the night rolling...we bring it!</p>
  </section>
</body>
</html>
```